Veldmark Supplies Business Card

Professional business card that stand out to our potential customers. Front and back with clean modern design

Industry/Entity Type

Oil and gas

Contact Information for Business Card

Name, address, website , office phone and cell number

Requirements
Must have
• Editable files for each employee

```html
<!DOCTYPE html>
<html lang="en">
<head>
<meta charset="utf-8">
<title>Veldmark Supplies Business Card</title>
<link href="https://fonts.googleapis.com/css2?family=Roboto:wght@400;500;700;900&display=swap" rel="stylesheet">
<style>
  :root {
    --backdrop: #2b2b2d;
    --card-black: #232325;
    --card-black-soft: #2e2e31;
    --brand-red: #e31e26;
    --brand-blue: #29b3d6;
    --ink-white: #ffffff;
    --ink-dark: #1a1a1a;
  }
  * { box-sizing: border-box; margin: 0; padding: 0; }
  html, body {
    width: 1200px; height: 852px; overflow: hidden;
    background: var(--backdrop);
    font-family: "Roboto", Arial, sans-serif;
  }
  .stage { position: relative; width: 1200px; height: 852px; }
  .card {
    position: absolute; width: 540px; height: 310px;
    border-radius: 22px; overflow: hidden;
  }
  /* Front card */
  .card--front {
    left: 80px; top: 100px;
    background: linear-gradient(135deg, var(--card-black-soft), var(--card-black));
    display: flex; align-items: center; justify-content: center;
  }
  .wordmark {
    display: flex; align-items: center; gap: 14px;
  }
  .wordmark__square {
    width: 28px; height: 28px; background: var(--brand-red);
  }
  .wordmark__name {
    font-weight: 900; font-size: 34px; letter-spacing: 1px;
    color: var(--brand-blue); text-transform: uppercase;
  }
  /* Back card */
  .card--back { left: 580px; top: 440px; background: var(--card-black); }
  .card__bands { position: absolute; inset: 0; }
  .card__header {
    position: absolute; left: 28px; top: 40px;
    font-weight: 900; font-size: 22px; letter-spacing: 1px;
    color: var(--brand-blue); text-transform: uppercase;
  }
  .person { position: absolute; left: 28px; top: 120px; color: var(--ink-white); }
  .person__name { font-weight: 700; font-size: 22px; }
  .person__role { font-weight: 400; font-size: 13px; margin-top: 3px; }
  .contact {
    position: absolute; left: 28px; top: 196px; list-style: none;
    color: var(--ink-white); font-size: 13px; line-height: 20px;
  }
  .contact__item { display: flex; align-items: center; gap: 8px; }
  .contact__icon { width: 12px; height: 12px; fill: var(--ink-white); flex: none; }
  .contact__address { margin-top: 4px; }
</style>
</head>
<body>
<main class="stage">
  <section class="card card--front" aria-label="Card front">
    <div class="wordmark">
      <span class="wordmark__square"></span>
      <span class="wordmark__name">Veldmark Supplies</span>
    </div>
  </section>

  <section class="card card--back" aria-label="Card back">
    <svg class="card__bands" viewBox="0 0 540 310" preserveAspectRatio="none" aria-hidden="true">
      <polygon points="0,102 300,102 300,160 0,160" fill="var(--brand-blue)"/>
      <polygon points="0,160 300,160 300,80 540,80 540,310 0,310" fill="var(--brand-red)"/>
      <polygon points="480,0 540,0 540,80 480,80" fill="var(--brand-blue)"/>
    </svg>
    <div class="card__header">Veldmark Supplies</div>
    <div class="person">
      <div class="person__name">Dale Ortmann</div>
      <div class="person__role">Managing Director</div>
    </div>
    <ul class="contact">
      <li class="contact__item">
        <svg class="contact__icon" viewBox="0 0 24 24"><path d="M6.6 10.8a15 15 0 0 0 6.6 6.6l2.2-2.2a1 1 0 0 1 1-.25 11.4 11.4 0 0 0 3.6.57 1 1 0 0 1 1 1V20a1 1 0 0 1-1 1A17 17 0 0 1 3 4a1 1 0 0 1 1-1h3.5a1 1 0 0 1 1 1c0 1.25.2 2.45.57 3.6a1 1 0 0 1-.25 1z"/></svg>
        (555)014-2290
      </li>
      <li class="contact__item">
        <svg class="contact__icon" viewBox="0 0 24 24"><path d="M2 5h20v14H2z M3 6l9 7 9-7" stroke="#e31e26" stroke-width="1.5"/></svg>
        sales@veldmarksupplies.com
      </li>
      <li class="contact__item">
        <svg class="contact__icon" viewBox="0 0 24 24"><circle cx="12" cy="12" r="10"/><path d="M2 12h20M12 2c3 3 3 17 0 20M12 2c-3 3-3 17 0 20" stroke="#e31e26" stroke-width="1.5" fill="none"/></svg>
        www.veldmarksupplies.com
      </li>
      <li class="contact__address">420 Harlow Ave Suite 3 Midvale, Tx 79012</li>
    </ul>
  </section>
</main>
</body>
</html>
```